Podiatry clinic requires a modern revamp and editing of existing website.

I would like a fresh new look and updated information for my current business website. An easy to navigate site with prominent address and phone number for call to action. We are a podiatry clinic that focuses on general and sports podiatry.
I would like 4 pages; including Home page, About Us, Services & Contact.
www.brambleridgepodiatry.net

Target Market(s)

Active working professionals.

Industry/Entity Type

Medical

Coding

Coded - Design and coding required

Number of Pages Required

4 page

Font styles to use
Sans Serif

Colors
6b449b

Requirements
Must have
• A modern look with logo and active images; clean and uncluttered. Visible phone number and address for call to action.
• 4 pages - Home, About Us, Services, Contact.
• Home page - update address & service logos.
• About Us - update of personal information.
• Services - Revamp of existing page.
• Contact page to include Google map, email & phone number.
Nice to have
• Ability to add content easily; eg. a blog or adding video onto Home page.
• Link to Facebook page.

```html
<!DOCTYPE html>
<html lang="en">
<head>
<meta charset="utf-8">
<title>Bramble Ridge Podiatry</title>
<link rel="stylesheet" href="https://fonts.googleapis.com/css2?family=Lato:wght@400;700&family=Raleway:wght@400;500;600;700&display=swap">
<style>
:root{
  --orange:#f26f21;
  --green:#7dbb2b;
  --purple:#4b2f8f;
  --ink:#1b1b1b;
  --text:#333333;
  --muted:#6b6b6b;
  --soft:#f5f5f5;
  --white:#ffffff;
  --night:#1d232c;
}
*{box-sizing:border-box;margin:0;padding:0}
html,body{width:1200px;height:2236px;overflow:hidden}
body{position:relative;background:var(--white);font-family:'Lato',sans-serif;color:var(--text)}
.abs{position:absolute}

/* header */
.site-header{position:absolute;left:0;top:0;width:1200px;height:130px;background:var(--white);box-shadow:0 2px 4px rgba(0,0,0,.25);z-index:2}
.brand{position:absolute;left:100px;top:30px;display:flex;align-items:center;gap:12px}
.brand-dot{width:28px;height:28px;border-radius:50%;background:var(--purple)}
.brand-name{font-family:'Raleway',sans-serif;font-weight:700;font-size:26px;line-height:1.1;color:var(--purple);width:150px}
.top-contact{position:absolute;top:28px;right:99px;display:flex;gap:30px;font-family:'Raleway',sans-serif;font-weight:600;font-size:14px;color:var(--ink);align-items:center}
.top-contact span{display:flex;align-items:center;gap:8px}
.chip{width:28px;height:28px;border-radius:50%;background:var(--green);display:inline-flex;align-items:center;justify-content:center}
.main-nav{position:absolute;left:450px;top:96px;display:flex;gap:56px;font-family:'Raleway',sans-serif;font-weight:600;font-size:16px;color:var(--ink)}
.main-nav .current{color:var(--purple)}
.book-btn{position:absolute;left:882px;top:86px;width:219px;height:32px;background:var(--orange);color:var(--white);font-family:'Raleway',sans-serif;font-weight:600;font-size:14px;display:flex;align-items:center;justify-content:center;gap:10px}

/* hero */
.hero{position:absolute;left:0;top:130px;width:1200px;height:468px;background:linear-gradient(120deg,#7a8796 0%,#c9b3a0 35%,#2a2a2a 55%,#e9e6e2 80%,#d8cfc6 100%)}
.hero-arrow{position:absolute;top:180px}
.hero-caption{position:absolute;left:0;bottom:0;width:100%;height:56px;background:rgba(20,20,20,.72);color:var(--white);font-family:'Raleway',sans-serif;font-weight:600;font-size:28px;display:flex;align-items:center;justify-content:center}

/* section headings */
.section-title{position:absolute;left:0;width:1200px;text-align:center;font-family:'Raleway',sans-serif;font-weight:700;font-size:32px;color:var(--ink)}
.section-title .o{color:var(--orange)}
.section-title .g{color:var(--green)}
.rule{position:absolute;left:310px;width:580px;height:1px;background:#bdbdbd}
.rule::after{content:"";position:absolute;left:273px;top:-1px;width:34px;height:3px;background:var(--orange)}

/* welcome */
.welcome-copy{position:absolute;left:100px;top:713px;width:1000px;text-align:center;font-family:'Raleway',sans-serif;font-size:14px;line-height:26.5px;color:var(--text)}
.read-more{position:absolute;left:544px;top:849px;width:111px;height:33px;background:var(--orange);border-radius:3px;color:var(--white);font-family:'Raleway',sans-serif;font-weight:600;font-size:12px;display:flex;align-items:center;justify-content:center}

/* treatments */
.treatments{position:absolute;left:0;top:926px;width:1200px;height:567px;background:var(--soft)}
.treat-intro{position:absolute;left:100px;top:1034px;width:1000px;text-align:center;font-size:17px;line-height:27px;color:var(--ink)}
.card{position:absolute;top:1131px;width:231px;height:273px;background:var(--white);border-bottom:3px solid var(--green);text-align:center}
.card.alt{border-bottom-color:var(--orange)}
.card-icon{position:absolute;left:77px;top:44px;width:77px;height:77px;border-radius:50%;background:var(--green);display:flex;align-items:center;justify-content:center}
.card.alt .card-icon{background:var(--orange)}
.card h3{position:absolute;left:0;top:152px;width:100%;font-family:'Raleway',sans-serif;font-weight:700;font-size:16px;color:var(--ink)}
.card p{position:absolute;left:12px;top:180px;width:207px;font-size:13px;line-height:22px;color:var(--ink)}
.card-plus{position:absolute;left:92px;bottom:-3px;width:48px;height:24px;border-radius:24px 24px 0 0;background:var(--green);color:var(--white);font-size:22px;line-height:26px}
.card.alt .card-plus{background:var(--orange)}
.slide-arrow{position:absolute;top:1258px}

/* inquiry */
.inquiry{position:absolute;left:0;top:1493px;width:1200px;height:280px;background:var(--orange)}
.inquiry h2{position:absolute;left:100px;top:70px;font-family:'Raleway',sans-serif;font-weight:700;font-size:35px;color:var(--white)}
.inquiry-copy{position:absolute;left:100px;top:134px;width:300px;font-family:'Raleway',sans-serif;font-size:13px;line-height:21px;color:#fde3d1}
.form-label{position:absolute;left:459px;top:48px;font-family:'Raleway',sans-serif;font-weight:600;font-size:15px;color:var(--white)}
.field{position:absolute;width:309px;height:41px;background:var(--white);border-radius:2px;font-family:'Raleway',sans-serif;font-size:12px;color:var(--muted);padding:13px 14px}
.submit{position:absolute;left:459px;top:186px;width:163px;height:42px;background:#111;border-radius:2px;color:var(--white);font-family:'Raleway',sans-serif;font-weight:700;font-size:17px;display:flex;align-items:center;justify-content:center}

/* footer */
.site-footer{position:absolute;left:0;top:1773px;width:1200px;height:463px;background:linear-gradient(180deg,#1f2a38 0%,#2b2f36 45%,#3a3429 75%,#1b1d22 100%);border-top:3px solid #2f5e9e}
.foot-contact{position:absolute;top:0;width:300px;text-align:center;color:var(--white);font-family:'Raleway',sans-serif;font-weight:600;font-size:14px}
.foot-contact .line{position:absolute;top:60px;height:1px;background:var(--green)}
.foot-contact .txt{position:absolute;left:0;top:91px;width:100%}
.foot-brand{position:absolute;left:0;top:160px;width:1200px;display:flex;justify-content:center;align-items:center;gap:14px}
.foot-brand .brand-dot{background:var(--white);width:34px;height:34px}
.foot-brand .brand-name{color:var(--white);font-size:32px;width:auto}
.foot-nav{position:absolute;left:0;top:339px;width:1200px;display:flex;justify-content:center;gap:22px;font-size:14px;color:var(--white)}
.foot-nav span+span::before{content:"•";margin-right:14px;color:#aaa;font-size:9px;vertical-align:middle}
.foot-bottom{position:absolute;left:0;top:380px;width:1200px;height:83px;border-top:1px solid rgba(255,255,255,.15)}
.copyright{position:absolute;left:100px;top:33px;font-size:13px;color:var(--white)}
.socials{position:absolute;left:914px;top:24px;display:flex;gap:15px}
.socials span{width:36px;height:36px;border-radius:50%;border:2px solid var(--white)}
</style>
</head>
<body>

<header class="site-header">
  <div class="brand"><span class="brand-dot"></span><span class="brand-name">Bramble Ridge Podiatry</span></div>
  <div class="top-contact">
    <span><i class="chip"><svg width="14" height="10" viewBox="0 0 14 10"><rect x=".5" y=".5" width="13" height="9" fill="none" stroke="#fff"/><path d="M.5 .5 7 6l6.5-5.5" fill="none" stroke="#fff"/></svg></i>info@brambleridgepodiatry.net</span>
    <span><i class="chip"><svg width="14" height="14" viewBox="0 0 24 24"><path d="M6.6 10.8a15 15 0 0 0 6.6 6.6l2.2-2.2a1 1 0 0 1 1-.25 11 11 0 0 0 3.6.6 1 1 0 0 1 1 1V20a1 1 0 0 1-1 1A17 17 0 0 1 3 4a1 1 0 0 1 1-1h3.5a1 1 0 0 1 1 1 11 11 0 0 0 .6 3.6 1 1 0 0 1-.25 1z" fill="#fff"/></svg></i>(310) 555-0148</span>
  </div>
  <nav class="main-nav"><span class="current">home</span><span>about us</span><span>services</span><span>contact us</span></nav>
  <div class="book-btn"><svg width="20" height="20" viewBox="0 0 20 20"><rect x="2" y="3" width="14" height="15" fill="none" stroke="#fff" stroke-width="1.5"/><circle cx="14" cy="14" r="5" fill="#f26f21" stroke="#fff" stroke-width="1.5"/><path d="M14 11.5V14h2" stroke="#fff" fill="none"/></svg>book an appointment</div>
</header>

<section class="hero" role="img" aria-label="Photo of a podiatrist stretching a patient's leg">
  <svg class="hero-arrow" style="left:48px" width="32" height="64" viewBox="0 0 32 64"><path d="M30 2 2 32l28 30" fill="none" stroke="#fff" stroke-width="2" opacity=".8"/></svg>
  <svg class="hero-arrow" style="left:1120px" width="32" height="64" viewBox="0 0 32 64"><path d="M2 2l28 30L2 62" fill="none" stroke="#fff" stroke-width="2" opacity=".8"/></svg>
  <div class="hero-caption">Bramble Ridge Podiatry is a Podiatry clinic in the heart of Melbourne</div>
</section>

<h1 class="section-title" style="top:636px">welcome to <span class="o">bramble ridge</span> podiatry <span class="g">clinic</span></h1>
<div class="rule" style="top:692px"></div>
<p class="welcome-copy">Lorem ipsum dolor sit amet, consectetuer adipiscing elit, sed diam nonummy nibh euismod tincidunt ut laoreet dolore magna aliquam erat volutpat. Ut wisi enim ad minim veniam, quis nostrud exerci tation ullamcorper suscipit lobortis nisl ut aliquip ex ea commodo consequat. Duis autem vel eum iriure dolor in hendrerit in vulputate velit esse molestie consequat, vel illum dolore eu feugiat nulla facilisis at vero eros et accumsan et iusto odio dignissim qui blandit praesent luptatum zzril delenit augue duis dolore te feugait nulla facilisi.</p>
<div class="read-more">read more</div>

<section class="treatments"></section>
<h2 class="section-title" style="top:953px">podiatry <span class="o">treatments</span></h2>
<div class="rule" style="top:1013px"></div>
<p class="treat-intro">Lorem ipsum dolor sit amet, consectetuer adipiscing elit, sed diam nonummy nibh euismod tincidunt ut laoreet dolore magna aliquam erat volutpat. Ut wisi enim ad minim veniam, quis nostrud exerci tation ullamcorper suscipit lobortis nisl ut</p>

<svg class="slide-arrow" style="left:51px" width="12" height="22" viewBox="0 0 12 22"><path d="M11 1 1 11l10 10" fill="none" stroke="#8f8fb8" stroke-width="2"/></svg>
<svg class="slide-arrow" style="left:1130px" width="12" height="22" viewBox="0 0 12 22"><path d="M1 1l10 10L1 21" fill="none" stroke="#8f8fb8" stroke-width="2"/></svg>

<article class="card" style="left:100px">
  <div class="card-icon"><svg width="40" height="40" viewBox="0 0 40 40"><path d="M8 20h24M20 8v24" stroke="#fff" stroke-width="4"/></svg></div>
  <h3>treadmill analysis</h3><p>Duis autem vel eum iriure dolor in hendrerit in vulputate</p><div class="card-plus">+</div>
</article>
<article class="card alt" style="left:356px">
  <div class="card-icon"><svg width="40" height="40" viewBox="0 0 40 40"><rect x="6" y="24" width="28" height="5" fill="#fff"/><circle cx="20" cy="13" r="5" fill="#fff"/></svg></div>
  <h3>orthotis therapy</h3><p>Duis autem vel eum iriure dolor in hendrerit in vulputate</p><div class="card-plus">+</div>
</article>
<article class="card" style="left:613px">
  <div class="card-icon"><svg width="40" height="40" viewBox="0 0 40 40"><ellipse cx="14" cy="24" rx="5" ry="9" fill="#fff"/><ellipse cx="27" cy="20" rx="5" ry="9" fill="#fff"/></svg></div>
  <h3>callus</h3><p>Duis autem vel eum iriure dolor in hendrerit in vulputate</p><div class="card-plus">+</div>
</article>
<article class="card alt" style="left:870px">
  <div class="card-icon"><svg width="40" height="40" viewBox="0 0 40 40"><path d="M6 14h18c6 0 10 4 10 9s-4 6-10 6H10c-3 0-4-3-4-6z" fill="#fff"/></svg></div>
  <h3>heel pain</h3><p>Duis autem vel eum iriure dolor in hendrerit in vulputate</p><div class="card-plus">+</div>
</article>

<section class="inquiry">
  <h2>quick inquiry</h2>
  <p class="inquiry-copy">Duis autem vel eum iriure dolormi opl inmokl hendi rerit in vulpu tateml velitm essemol mo molestiel conseqb uat, velmi illum dolor eokf no atn nulla more facilisis... [+]</p>
  <div class="form-label">please fill up bellow form</div>
  <div class="field" style="left:459px;top:84px">name</div>
  <div class="field" style="left:792px;top:84px">email</div>
  <div class="field" style="left:459px;top:135px">phone</div>
  <div class="field" style="left:792px;top:135px">message</div>
  <div class="submit">submit</div>
</section>

<footer class="site-footer" role="img" aria-label="Night skyline of the city with river and lit towers">
  <div class="foot-contact" style="left:160px">
    <i class="line" style="left:14px;width:118px"></i>
    <svg class="abs" style="left:141px;top:46px" width="18" height="26" viewBox="0 0 18 26"><path d="M9 25S1 14 1 9a8 8 0 0 1 16 0c0 5-8 16-8 16z" fill="none" stroke="#ddd" stroke-width="1.4"/><circle cx="9" cy="9" r="3" fill="none" stroke="#ddd" stroke-width="1.4"/></svg>
    <i class="line" style="left:168px;width:118px"></i>
    <div class="txt">Suite 12/88 Larkin Street Melbourne 3000</div>
  </div>
  <div class="foot-contact" style="left:456px">
    <i class="line" style="left:10px;width:122px"></i>
    <svg class="abs" style="left:138px;top:47px" width="24" height="24" viewBox="0 0 24 24"><path d="M6.6 10.8a15 15 0 0 0 6.6 6.6l2.2-2.2a1 1 0 0 1 1-.25 11 11 0 0 0 3.6.6 1 1 0 0 1 1 1V20a1 1 0 0 1-1 1A17 17 0 0 1 3 4a1 1 0 0 1 1-1h3.5a1 1 0 0 1 1 1 11 11 0 0 0 .6 3.6 1 1 0 0 1-.25 1z" fill="none" stroke="#ddd" stroke-width="1.3"/></svg>
    <i class="line" style="left:172px;width:118px"></i>
    <div class="txt">Phone: 1300 482 907</div>
  </div>
  <div class="foot-contact" style="left:740px">
    <i class="line" style="left:20px;width:118px"></i>
    <svg class="abs" style="left:138px;top:47px" width="26" height="24" viewBox="0 0 26 24"><path d="M25 1 1 10l9 3 2 9 4-6 6 4z M10 13 25 1" fill="none" stroke="#ddd" stroke-width="1.3"/></svg>
    <i class="line" style="left:172px;width:118px"></i>
    <div class="txt">Email: info@brambleridgepodiatry.net</div>
  </div>
  <div class="foot-brand"><span class="brand-dot"></span><span class="brand-name">Bramble Ridge Podiatry</span></div>
  <nav class="foot-nav"><span>home</span><span>about us</span><span>services</span><span>contact us</span></nav>
  <div class="foot-bottom">
    <div class="copyright">Copyright © 2016 Bramble Ridge Podiatry. All Right Reserved.</div>
    <div class="socials"><span style="background:#3b5998"></span><span style="background:#0e76a8"></span><span style="background:#1da1f2"></span><span style="background:#d34836"></span></div>
  </div>
</footer>

</body>
</html>
```